Dovecote Realty

Business cards for 4 people

They need to say for all
87 Tarrow Quay, Boston MA 02114

Each person will have their own personal information
We would like gold embossing for the name of the company
Marla is the blonde sitting in the chair smiling her information should be on the back of the card with her name and information
Should say for slogan classic pattern, elevated experience
grace@dovecoteprops.com
(413) 555-0182

Odette is the brunette with wavy hair in the tan suit odette@dovecoteprops.com
(617) 555-0137

faith@dovecoteprops.com
(413) 555-0164
standing next to the chair

hope@dovecoteprops.com
(413) 555-0199
close up headshot

```html
<!DOCTYPE html>
<html lang="en">
<head>
<meta charset="UTF-8">
<title>Dovecote Realty Business Cards</title>
<link href="https://fonts.googleapis.com/css2?family=Open+Sans:wght@400;600;700&display=swap" rel="stylesheet">
<style>
  :root {
    --backdrop: #222222;
    --navy: #22314f;
    --navy-emboss: #2f4677;
    --gold: #e9b654;
    --white: #ffffff;
    --photo-light: #a07650;
    --photo-dark: #3a3f55;
  }
  * { margin: 0; padding: 0; box-sizing: border-box; }
  html, body {
    width: 1200px; height: 780px; overflow: hidden;
    background: var(--backdrop);
    font-family: "Open Sans", Arial, sans-serif;
  }
  .stage {
    width: 1200px; height: 780px;
    display: flex; align-items: center; justify-content: center; gap: 40px;
  }
  .card {
    position: relative;
    width: 540px; height: 310px;
    background: var(--navy);
    overflow: hidden;
    box-shadow: 0 10px 30px rgba(0,0,0,.45);
  }
  /* Front */
  .card-front .portrait {
    position: absolute; left: 0; top: 0; bottom: 0; width: 235px;
    background: linear-gradient(160deg, var(--photo-dark) 0%, var(--photo-light) 45%, #8a5f3d 100%);
  }
  .card-front .details {
    position: absolute; right: 40px; top: 34px;
    text-align: right; color: var(--white);
  }
  .brand-name {
    display: block;
    color: var(--gold); font-weight: 600; font-size: 17px; letter-spacing: 2px;
    text-transform: uppercase; line-height: 1.2;
  }
  .agent-name {
    margin-top: 16px;
    color: var(--gold); font-weight: 700; font-size: 27px; line-height: 1.1;
  }
  .agent-title { font-size: 11px; margin-top: 3px; }
  .address { font-size: 14px; margin-top: 16px; line-height: 1.3; }
  .contacts { list-style: none; margin-top: 10px; font-size: 13px; line-height: 1.55; }
  .contacts li { display: flex; align-items: center; justify-content: flex-end; gap: 8px; }
  .contacts svg { width: 13px; height: 13px; fill: var(--gold); flex: none; }
  .accent-bar {
    position: absolute; right: 0; top: 82px; width: 22px; height: 50px;
    background: var(--gold);
  }
  /* Back */
  .card-back {
    display: flex; align-items: center; justify-content: center;
  }
  .emboss-name {
    color: var(--navy-emboss); font-weight: 600; font-size: 38px;
    letter-spacing: 4px; text-transform: uppercase;
  }
</style>
</head>
<body>
<main class="stage">
  <section class="card card-front">
    <div class="portrait" role="img" aria-label="Portrait photo of Odette, brunette with wavy hair in a tan suit"></div>
    <div class="details">
      <span class="brand-name">Dovecote Realty</span>
      <h1 class="agent-name">Odette Marchand</h1>
      <p class="agent-title">Real Estate Advisor and Sales Manager</p>
      <p class="address">87 Tarrow Quay,<br>Boston MA 02114</p>
      <ul class="contacts">
        <li>(617) 555-0137
          <svg viewBox="0 0 24 24"><path d="M6.6 10.8a15 15 0 0 0 6.6 6.6l2.2-2.2c.3-.3.7-.4 1-.2 1.1.4 2.3.6 3.6.6.6 0 1 .4 1 1V20c0 .6-.4 1-1 1A17 17 0 0 1 3 4c0-.6.4-1 1-1h3.5c.6 0 1 .4 1 1 0 1.3.2 2.5.6 3.6.1.3 0 .7-.2 1z"/></svg></li>
        <li>www.dovecoteprops.com
          <svg viewBox="0 0 24 24"><path d="M12 2a10 10 0 1 0 0 20 10 10 0 0 0 0-20zm6.9 6h-2.9a15 15 0 0 0-1.4-3.6A8 8 0 0 1 18.9 8zM12 4c.8 1.2 1.5 2.5 1.9 4h-3.8c.4-1.5 1.1-2.8 1.9-4zM4.3 14a8 8 0 0 1 0-4h3.4a16 16 0 0 0 0 4zm.8 2h2.9c.3 1.3.8 2.5 1.4 3.6A8 8 0 0 1 5.1 16zM8 8H5.1a8 8 0 0 1 4.3-3.6C8.8 5.5 8.3 6.7 8 8zm4 12c-.8-1.2-1.5-2.5-1.9-4h3.8c-.4 1.5-1.1 2.8-1.9 4zm2.3-6H9.7a14 14 0 0 1 0-4h4.6a14 14 0 0 1 0 4zm.3 5.6c.6-1.1 1.1-2.3 1.4-3.6h2.9a8 8 0 0 1-4.3 3.6zm1.7-5.6a16 16 0 0 0 0-4h3.4a8 8 0 0 1 0 4z"/></svg></li>
        <li>odette@dovecoteprops.com
          <svg viewBox="0 0 24 24"><path d="M3 5h18c.6 0 1 .4 1 1v12c0 .6-.4 1-1 1H3c-.6 0-1-.4-1-1V6c0-.6.4-1 1-1zm9 7.5L4.5 7v1.9L12 14l7.5-5.1V7z"/></svg></li>
      </ul>
    </div>
    <div class="accent-bar"></div>
  </section>

  <section class="card card-back">
    <span class="emboss-name">Dovecote Realty</span>
  </section>
</main>
</body>
</html>
```